Marine Services Letterhead design

We need a letterhead design for an Australian owned company in Victoria named K+T Harbour Works Pty Ltd. We provide linesmen and launches to assist the large ships that come into port.
Our colour is orange.
The final design should have a strong nautical theme and communicate safety and reliability.
I would like to use the letter head on invoices so it should print to pdf well.

Target Market(s)

Owners and representatives of shipping companies. It is not for general public

Industry/Entity Type

Nautical

Requirements
Must have
• A shipping theme, not overly complicated, featuring safety orange colours but not all orange of course.
The letterhead should just sit at the top of the page so I can use for invoices.
Nice to have
• Something elegant and stylish
Should not have
• cartoons or pop art

```html
<!DOCTYPE html>
<html lang="en">
<head>
<meta charset="utf-8">
<title>K+T Harbour Works Pty Ltd — Letterhead</title>
<link rel="stylesheet" href="https://fonts.googleapis.com/css2?family=Source+Sans+3:wght@400;600&display=swap">
<style>
  :root {
    --paper: #ffffff;
    --brand-orange: #b0692c;
    --name-orange: #bd7a3a;
    --mark-fill: #d9a25f;
    --mark-panel: #f2f2f2;
    --ink: #111111;
    --footer-text: #ffffff;
  }
  * { margin: 0; padding: 0; box-sizing: border-box; }
  html, body {
    width: 926px;
    height: 1200px;
    overflow: hidden;
    background: var(--paper);
  }
  .letterhead {
    position: relative;
    width: 926px;
    height: 1200px;
    background: var(--paper);
    font-family: "Source Sans 3", "Myriad Pro", sans-serif;
  }
  .brand {
    position: absolute;
    top: 3px;
    left: 289px;
    width: 306px;
    text-align: center;
  }
  .brand-panel {
    width: 306px;
    height: 235px;
    background: var(--mark-panel);
    display: flex;
    align-items: center;
    justify-content: center;
  }
  .brand-square {
    width: 170px;
    height: 170px;
    background: var(--mark-fill);
  }
  .brand-name {
    margin-top: 2px;
    font-size: 19px;
    font-weight: 600;
    color: var(--name-orange);
    letter-spacing: 0.1px;
  }
  .footer-wave {
    position: absolute;
    left: 0;
    top: 0;
    width: 926px;
    height: 1200px;
    pointer-events: none;
  }
  .contact {
    position: absolute;
    right: 22px;
    top: 1076px;
    list-style: none;
    text-align: right;
    color: var(--footer-text);
    font-size: 19px;
    line-height: 1;
  }
  .contact li {
    display: flex;
    justify-content: flex-end;
    align-items: center;
    gap: 5px;
    height: 19px;
    margin-bottom: 19.5px;
  }
  .contact svg { width: 17px; height: 17px; flex: none; }
</style>
</head>
<body>
<main class="letterhead">
  <header class="brand">
    <div class="brand-panel">
      <div class="brand-square"></div>
    </div>
    <p class="brand-name">K+T Harbour Works Pty Ltd</p>
  </header>

  <svg class="footer-wave" viewBox="0 0 926 1200" aria-hidden="true">
    <path d="M0,1176 C180,1190 380,1180 545,1142 C705,1098 812,1022 926,1008 L926,1200 L0,1200 Z"
          fill="var(--brand-orange)"/>
    <path d="M0,1113 C150,1150 320,1166 480,1132 C650,1092 780,1008 926,996 L926,1002 C790,1016 660,1102 495,1146 C330,1186 150,1172 0,1146 Z"
          fill="var(--ink)"/>
    <path d="M100,1163 C260,1175 400,1170 520,1150" fill="none" stroke="var(--ink)" stroke-width="2"/>
  </svg>

  <ul class="contact">
    <li>
      <svg viewBox="0 0 20 20" aria-hidden="true">
        <circle cx="10" cy="10" r="8.6" fill="none" stroke="#fff" stroke-width="1.6"/>
        <path d="M7 5.5 L8.8 7.6 L7.9 9 C8.6 10.5 9.6 11.5 11 12.2 L12.4 11.2 L14.5 13 L13.3 14.6 C10 14.4 5.8 10.2 5.5 6.8 Z" fill="#fff"/>
      </svg>
      <span>1300 555 018</span>
    </li>
    <li><span>ABN: 48102736615</span></li>
    <li>
      <svg viewBox="0 0 20 20" aria-hidden="true">
        <path d="M10 1 C6.4 1 4 3.6 4 7 C4 11.5 10 19 10 19 C10 19 16 11.5 16 7 C16 3.6 13.6 1 10 1 Z M10 9.4 A2.4 2.4 0 1 1 10 4.6 A2.4 2.4 0 1 1 10 9.4 Z" fill="#fff"/>
      </svg>
      <span>PO Box 214 Seabrook 3928</span>
    </li>
  </ul>
</main>
</body>
</html>
```